Tide & Thistle Website Creation For Online Spirits Sales via MerrowVats.com

Want a Website developed that I will use to partner with Merrow Vats to sell my signature rum online. Merrow Vats will add the final code to make the website an e-commerce site. Website should have links to Social media pages, recipies, About, news and events, products. I have he domain name already just need a designer to make the website look professional. Need website capable of being viewed on iPhone and Android devices. Please use the color scheme that is on the label. The brand motto is: Celebrate Life With Family old and new friends. The bottle sent in the images will be replaced with and actual high resolution image of the bottle when it is produce on 27 DEC 21. Can give the selected designer access to develop the website. I have the hostbramble.com domain name. Final code will be added by a designer from MerrowVats.com to make it a e-commerce store.
Updates

I added more information to refine the design I wanted. I should have had this information available to the designers when I started the project.

Target Market(s)

Target Market is 25-50 year old who drink rum

Industry/Entity Type

Spirits. Using Website to sell Rum online

Number of Pages Required

1 page

Font styles to use
Sans Serif

Colors
00AB8E
00BBA5
67D7C9
C6EFE9
E9F9F6

Requirements
Must have
• Must look elegant and of high class. Rum is being market as a premium unnamed rum.
Nice to have
• Video of people drinking, smiling and celebrating

```html
<!DOCTYPE html>
<html lang="en">
<head>
<meta charset="utf-8">
<title>Tide &amp; Thistle — Small Batch Crafted Rum</title>
<link rel="stylesheet" href="https://fonts.googleapis.com/css2?family=Cinzel:wght@400;600;700&family=Great+Vibes&family=Montserrat:wght@400;500;600;700&display=swap">
<style>
:root{
  --teal-deep:#00AB8E;
  --teal:#00BBA5;
  --teal-soft:#67D7C9;
  --mint:#C6EFE9;
  --mint-pale:#E9F9F6;
  --ink:#1d1d1d;
  --text:#555;
  --footer:#1c0b0e;
  --orange:#f26522;
  --white:#fff;
}
*{box-sizing:border-box;margin:0;padding:0}
html,body{width:1200px;height:3927px;overflow:hidden}
body{position:relative;background:var(--white);font-family:"Montserrat",Arial,sans-serif;color:var(--ink)}
.abs{position:absolute}
.vline{position:absolute;width:2px;background:var(--teal);left:599px}

/* header */
.site-header{position:absolute;left:0;top:0;width:1200px;height:84px;background:var(--white)}
.brand{position:absolute;left:110px;top:9px;display:flex;align-items:center;gap:12px}
.brand-dot{width:64px;height:64px;border-radius:50%;background:var(--ink)}
.brand-name{font-family:"Cinzel",Georgia,serif;font-size:29px;font-weight:600;color:var(--ink);letter-spacing:.5px}
.main-nav a{position:absolute;top:36px;font-size:12px;font-weight:500;color:var(--ink);text-decoration:none;transform:translateX(-50%);white-space:nowrap}
.main-nav a.active{color:var(--teal-deep);font-weight:600}
.main-nav a.active::after{content:"";position:absolute;left:-8px;right:-8px;top:45px;height:2px;background:var(--teal-deep)}
.header-icon{position:absolute;top:30px}

/* hero */
.hero{position:absolute;left:0;top:84px;width:1200px;height:672px;
  background:radial-gradient(ellipse at 70% 40%,#8a8a86 0%,#4a4a48 35%,transparent 65%),
  linear-gradient(180deg,#2e2d2b 0%,#3d3a35 55%,#8b6a48 75%,#5d4a38 100%)}
.hero-script{position:absolute;left:113px;top:257px;font-family:"Great Vibes",cursive;font-size:66px;color:var(--white);line-height:1}
.hero-title{position:absolute;left:113px;top:334px;font-family:"Cinzel",Georgia,serif;font-weight:600;font-size:56px;line-height:56px;color:var(--white);letter-spacing:1px}
.btn-outline-white{position:absolute;left:125px;top:477px;width:189px;height:48px;border:2px solid var(--white);color:var(--white);font-size:15px;font-weight:700;display:flex;align-items:center;justify-content:center}
.play{position:absolute;left:769px;top:330px}

/* about */
.about-visual{position:absolute;left:117px;top:869px;width:452px;height:452px;border-radius:50%;
  background:linear-gradient(135deg,#2a6f9a 0%,#4fa3c8 40%,#c77a3c 75%,#e2a14f 100%)}
.about-ring{position:absolute;left:117px;top:869px}
.section-script{position:absolute;font-family:"Great Vibes",cursive;color:var(--teal);font-size:40px;line-height:1;white-space:nowrap}
.section-title{position:absolute;font-family:"Cinzel",Georgia,serif;font-weight:600;font-size:36px;color:var(--ink);letter-spacing:.5px;line-height:1;white-space:nowrap}
.underline{position:absolute;height:2px;background:var(--teal);width:72px}
.about-copy{position:absolute;left:657px;width:450px;font-size:13.5px;line-height:23px;color:var(--text)}
.btn-learn{position:absolute;left:657px;top:1222px;width:190px;height:48px;background:var(--teal-deep);color:var(--white);font-size:15px;font-weight:700;display:flex;align-items:center;justify-content:center}
.btn-learn-shadow{position:absolute;left:665px;top:1230px;width:190px;height:48px;border:2px solid var(--teal-deep)}

/* products */
.products{position:absolute;left:0;top:1440px;width:1200px;height:760px;background:var(--mint-pale)}
.product{position:absolute;width:260px;text-align:center;transform:translateX(-50%)}
.product-media{width:170px;height:282px;margin:0 auto;border-radius:10px;
  background:linear-gradient(180deg,#eef6f3 0%,#e3b27a 45%,#c0622c 80%,#9d4a1e 100%)}
.product-name{margin-top:32px;font-size:17px;font-weight:600;color:#333;letter-spacing:.3px}
.product-desc{margin-top:8px;font-size:12.5px;color:var(--text)}
.btn-pill{display:inline-flex;align-items:center;justify-content:center;width:146px;height:38px;border:2px solid var(--teal);border-radius:20px;color:var(--teal);font-size:12px;font-weight:700;margin-top:18px;background:transparent}
.arrow{position:absolute}

/* recipes */
.recipes{position:absolute;left:0;top:2130px;width:1200px;height:725px;
  background:linear-gradient(100deg,var(--teal-deep) 0%,var(--teal) 50%,var(--teal-soft) 100%)}
.torn{position:absolute;left:0;top:2118px}
.recipe-card{position:absolute;text-align:center}
.recipe-card.side{border:2px solid var(--white);border-top:0;color:var(--white)}
.recipe-card.feature{background:var(--white);box-shadow:0 10px 30px rgba(0,0,0,.18);color:#333}
.recipe-media{width:100%}
.recipe-title{font-size:16px;font-weight:600;margin-top:16px;white-space:nowrap}
.recipe-card.side .recipe-title{color:var(--white)}
.recipe-steps{font-size:12.5px;line-height:21px;margin-top:10px}
.recipe-card.side .recipe-steps{color:rgba(255,255,255,.9)}
.recipe-card.feature .recipe-steps{color:var(--text);font-size:13px;line-height:22px}
.btn-pill.light{border-color:var(--white);color:var(--white);width:130px;height:34px;font-size:10.5px;margin-top:14px}
.btn-pill.soft{background:var(--mint-pale);border-color:var(--mint-pale);color:var(--teal-deep);width:136px;height:34px;font-size:10.5px;margin-top:16px}

/* news */
.news-lead{position:absolute;left:133px;top:3036px;width:485px;height:380px;
  background:radial-gradient(circle at 75% 35%,#7fbf3a 0%,#3f7d22 28%,#1d1f1d 60%,#111 100%)}
.date{position:absolute;background:var(--orange);color:var(--white);font-size:11px;font-weight:600;padding:4px 12px}
.news-lead-title{position:absolute;left:172px;top:3350px;width:420px;font-size:17px;font-weight:700;line-height:21px;color:var(--white)}
.news-card{position:absolute;left:627px;width:448px;height:184px;background:var(--white);border:1px solid var(--mint)}
.news-card .media{position:absolute;left:0;top:0;width:215px;height:100%}
.news-card .date{left:238px;top:34px;font-size:10px;padding:3px 12px}
.news-card h3{position:absolute;left:238px;top:66px;font-size:12.5px;font-weight:700;color:#333}
.news-card p{position:absolute;left:238px;top:90px;width:195px;font-size:12px;line-height:20px;color:var(--text)}

/* footer */
.site-footer{position:absolute;left:0;top:3518px;width:1200px;height:409px;background:var(--footer);color:var(--white)}
.footer-brand-dot{position:absolute;left:214px;top:69px;width:70px;height:70px;border-radius:50%;border:3px solid var(--white)}
.footer-brand-name{position:absolute;left:249px;top:148px;transform:translateX(-50%);font-family:"Cinzel",Georgia,serif;font-weight:600;font-size:32px;white-space:nowrap}
.social{position:absolute;top:209px;width:36px;height:36px;border-radius:50%;border:2px solid var(--teal)}
.footer-divider{position:absolute;top:75px;width:1px;height:45px;background:rgba(255,255,255,.35)}
.footer-heading{position:absolute;top:86px;font-family:"Cinzel",Georgia,serif;font-weight:600;font-size:16px;letter-spacing:.5px}
.footer-links{position:absolute;top:125px;list-style:none;font-size:12.5px}
.footer-links li{height:29px}
.contact-row{position:absolute;left:944px;font-size:12.5px;line-height:18px}
.contact-icon{position:absolute;left:914px}
.footer-rule{position:absolute;left:0;top:351px;width:1200px;height:1px;background:rgba(255,255,255,.15)}
.copyright{position:absolute;left:0;top:368px;width:1200px;text-align:center;font-size:11px;color:rgba(255,255,255,.85)}
</style>
</head>
<body>

<header class="site-header">
  <div class="brand"><span class="brand-dot"></span><span class="brand-name">TIDE &amp; THISTLE</span></div>
  <nav class="main-nav">
    <a href="#about" class="active" style="left:537px">ABOUT US</a>
    <a href="#products" style="left:659px">PRODUCTS</a>
    <a href="#recipes" style="left:775px">RECIPIES</a>
    <a href="#news" style="left:903px">NEWS &amp; EVENT</a>
  </nav>
  <svg class="header-icon" style="left:1019px" width="20" height="20" viewBox="0 0 20 20" aria-label="Search"><circle cx="8" cy="8" r="6" fill="none" stroke="#444" stroke-width="1.6"/><line x1="12.5" y1="12.5" x2="18" y2="18" stroke="#444" stroke-width="1.6"/></svg>
  <svg class="header-icon" style="left:1064px" width="20" height="20" viewBox="0 0 20 20" aria-label="Cart"><rect x="3" y="5" width="14" height="13" fill="none" stroke="#444" stroke-width="1.6"/><path d="M7 5V3h6v2" fill="none" stroke="#444" stroke-width="1.6"/></svg>
</header>

<section class="hero" role="img" aria-label="Bartender pouring rum from a shaker into a crystal glass on a wooden board with orange peel and rosemary"></section>
<div class="hero-script">Caribbean Rum</div>
<div class="hero-title">SMALL BATCH<br>CRAFTED RUM</div>
<div class="btn-outline-white">SHOP NOW</div>
<svg class="play" width="90" height="90" viewBox="0 0 90 90" aria-label="Play video"><circle cx="45" cy="45" r="45" fill="#fff"/><path d="M36 28 L62 45 L36 62 Z" fill="#222"/></svg>
<div class="vline" style="top:716px;height:77px"></div>

<section id="about">
  <div class="about-visual" role="img" aria-label="Friends laughing together outdoors, framed in a circular window"></div>
  <svg class="about-ring" width="452" height="452" viewBox="0 0 452 452" aria-hidden="true">
    <circle cx="226" cy="226" r="200" fill="none" stroke="#fff" stroke-width="14"/>
    <rect x="219" y="0" width="14" height="40" fill="#fff"/>
    <rect x="0" y="219" width="40" height="14" fill="#fff"/>
    <rect x="412" y="219" width="40" height="14" fill="#fff"/>
    <rect x="219" y="412" width="14" height="40" fill="#fff"/>
  </svg>
  <div class="section-script" style="left:642px;top:906px">Who we are</div>
  <div class="section-title" style="left:654px;top:954px">ABOUT TIDE &amp; THISTLE</div>
  <div class="underline" style="left:654px;top:1000px;width:60px"></div>
  <p class="about-copy" style="top:1028px">Lorem ipsum dolor sit amet, consectetur adipiscing elit, sed do eiusmod tempor incididunt ut labore et dolore magna aliqua. Ut enim ad minim veniam, quis nostrud exercitation ullamco laboris nisi ut aliquip ex ea commodo consequat.</p>
  <p class="about-copy" style="top:1142px">Duis aute irure dolor in reprehenderit in voluptate velit esse cillum dolore eu fugiat nulla pariatur. Excepteur sint occaecat</p>
  <div class="btn-learn-shadow"></div>
  <div class="btn-learn">LEARN MORE</div>
</section>

<section class="products" id="products"></section>
<div class="vline" style="top:1412px;height:75px"></div>
<div class="section-script" style="left:600px;top:1496px;transform:translateX(-50%)">Shop now</div>
<div class="section-title" style="left:600px;top:1544px;transform:translateX(-50%)">OUR PRODUCTS</div>
<div class="underline" style="left:564px;top:1588px"></div>

<div class="product" style="left:278px;top:1647px">
  <div class="product-media" role="img" aria-label="Bottle of red rum beside a glass on ice"></div>
  <div class="product-name">TIDE &amp; THISTLE RUM</div>
  <div class="product-desc">Lorem ipsum dolor sit amet conse</div>
  <span class="btn-pill">SHOP NOW</span>
</div>
<div class="product" style="left:607px;top:1647px">
  <div class="product-media" role="img" aria-label="Bottle of gold rum beside a glass on ice"></div>
  <div class="product-name">TIDE &amp; THISTLE RUM</div>
  <div class="product-desc">Lorem ipsum dolor sit amet conse</div>
  <span class="btn-pill">SHOP NOW</span>
</div>
<div class="product" style="left:938px;top:1647px">
  <div class="product-media" role="img" aria-label="Bottle of dark rum beside a glass on ice"></div>
  <div class="product-name">TIDE &amp; THISTLE RUM</div>
  <div class="product-desc">Lorem ipsum dolor sit amet conse</div>
  <span class="btn-pill" style="margin-top:30px">SHOP NOW</span>
</div>
<svg class="arrow" style="left:99px;top:1816px" width="24" height="40" viewBox="0 0 24 40" aria-label="Previous"><path d="M20 4 L5 20 L20 36" fill="none" stroke="#8a8a8a" stroke-width="4"/></svg>
<svg class="arrow" style="left:1110px;top:1816px" width="24" height="40" viewBox="0 0 24 40" aria-label="Next"><path d="M4 4 L19 20 L4 36" fill="none" stroke="#8a8a8a" stroke-width="4"/></svg>

<section class="recipes" id="recipes"></section>
<svg class="torn" width="1200" height="50" viewBox="0 0 1200 50" preserveAspectRatio="none" aria-hidden="true">
  <path d="M0 30 L40 26 L90 32 L150 24 L210 30 L280 22 L340 28 L420 20 L500 27 L580 19 L660 26 L740 18 L820 24 L900 17 L980 23 L1060 16 L1130 22 L1200 15 L1200 50 L0 50 Z" fill="#00AB8E"/>
</svg>
<div class="section-title" style="left:600px;top:2232px;transform:translateX(-50%);color:#fff">OUR RECIEPES</div>
<div class="underline" style="left:566px;top:2274px;background:#fff;width:66px"></div>

<article class="recipe-card side" style="left:163px;top:2350px;width:281px;height:387px">
  <div class="recipe-media" style="height:212px;background:linear-gradient(135deg,#2b1a10 0%,#7a4a22 55%,#d89a50 100%)" role="img" aria-label="Rum bottle and two tumblers on a rustic wooden table"></div>
  <div class="recipe-title">HARBOR OLD FASHIONED</div>
  <div class="recipe-steps">Pour all ingredients in a shaker<br>Shake vigorously 10 seconds<br>Pour in glass/ Ice ball</div>
  <span class="btn-pill light">LEARN MORE</span>
</article>
<article class="recipe-card side" style="left:772px;top:2350px;width:291px;height:387px">
  <div class="recipe-media" style="height:212px;background:linear-gradient(135deg,#c9c3b4 0%,#8a9a6e 45%,#d7a24a 100%)" role="img" aria-label="Rum punch tumblers with lime wedges and mint"></div>
  <div class="recipe-title">TIDE &amp; THISTLE RUM PUNCH</div>
  <div class="recipe-steps">Pour all ingredients in a shaker<br>Shake vigorously 10 seconds<br>Pour in glass w/ Crushed Ice</div>
  <span class="btn-pill light">LEARN MORE</span>
</article>
<article class="recipe-card feature" style="left:444px;top:2320px;width:328px;height:448px">
  <div class="recipe-media" style="height:236px;background:linear-gradient(135deg,#3f4a46 0%,#6f7f63 45%,#c7c98a 70%,#3c4640 100%)" role="img" aria-label="Pale cocktail in a coupe glass garnished with lime"></div>
  <div class="recipe-title" style="font-size:19px;margin-top:30px">CRANBERRY BREEZE</div>
  <div class="recipe-steps" style="margin-top:16px">Pour all ingredients in a shaker<br>Shake vigorously 10 seconds<br>Pour Mix in Highball Glass</div>
  <span class="btn-pill soft">LEARN MORE</span>
</article>
<svg class="arrow" style="left:94px;top:2522px" width="24" height="40" viewBox="0 0 24 40" aria-label="Previous"><path d="M20 4 L5 20 L20 36" fill="none" stroke="#fff" stroke-width="5"/></svg>
<svg class="arrow" style="left:1097px;top:2522px" width="24" height="40" viewBox="0 0 24 40" aria-label="Next"><path d="M4 4 L19 20 L4 36" fill="none" stroke="#fff" stroke-width="5"/></svg>

<section id="news">
  <div class="vline" style="top:2824px;height:78px"></div>
  <div class="section-script" style="left:604px;top:2908px;transform:translateX(-50%);font-size:36px">Latest update</div>
  <div class="section-title" style="left:604px;top:2954px;transform:translateX(-50%)">NEWS &amp; EVENT</div>
  <div class="underline" style="left:568px;top:2999px"></div>

  <div class="news-lead" role="img" aria-label="Limes, mint and crushed ice on a dark surface"></div>
  <span class="date" style="left:172px;top:3310px">28 MAY 2021</span>
  <div class="news-lead-title">Lorem ipsum dolor sit amet, consectetur adipiscing elit, sed do eiusmod tempor</div>

  <article class="news-card" style="top:3036px">
    <div class="media" role="img" aria-label="Red cocktail with orange slice at a bar" style="background:linear-gradient(135deg,#1a2140 0%,#7a2a20 50%,#c2462a 100%)"></div>
    <span class="date">19 MAY 2021</span>
    <h3>Lorem ipsum dolor sit</h3>
    <p>Duis aute irure dolor in repre-henderit in voluptate velit esse cillum dolore eu fugiat</p>
  </article>
  <article class="news-card" style="top:3233px">
    <div class="media" role="img" aria-label="Rum poured into snifter glasses on a dark table" style="background:linear-gradient(135deg,#1e1a18 0%,#4a3020 55%,#8a4a20 100%)"></div>
    <span class="date">18 MAY 2021</span>
    <h3>Lorem ipsum dolor sit</h3>
    <p>Duis aute irure dolor in repre-henderit in voluptate velit esse cillum dolore eu fugiat</p>
  </article>
</section>

<footer class="site-footer">
  <span class="footer-brand-dot"></span>
  <div class="footer-brand-name">TIDE &amp; THISTLE</div>
  <span class="social" style="left:168px" aria-label="Social profile"></span>
  <span class="social" style="left:212px" aria-label="Social profile"></span>
  <span class="social" style="left:256px" aria-label="Social profile"></span>
  <span class="social" style="left:301px" aria-label="Social profile"></span>

  <span class="footer-divider" style="left:419px"></span>
  <span class="footer-divider" style="left:659px"></span>
  <span class="footer-divider" style="left:874px"></span>

  <div class="footer-heading" style="left:448px">QUICK LINKS</div>
  <ul class="footer-links" style="left:453px"><li>About Us</li><li>Receipes</li><li>Products</li><li>News &amp; Events</li></ul>

  <div class="footer-heading" style="left:694px">RESOURCES</div>
  <ul class="footer-links" style="left:695px"><li>Shipping &amp; Return</li><li>Support</li><li>Privacy Policy</li><li>Contact</li></ul>

  <div class="footer-heading" style="left:909px">CONTACT US</div>
  <svg class="contact-icon" style="top:127px" width="16" height="20" viewBox="0 0 16 20" aria-label="Address"><path d="M8 0C3.6 0 0 3.4 0 7.6 0 13 8 20 8 20s8-7 8-12.4C16 3.4 12.4 0 8 0z" fill="#00BBA5"/><circle cx="8" cy="7.5" r="3" fill="#1c0b0e"/></svg>
  <div class="contact-row" style="top:125px">48 Harbor Lane<br>Port Wren, IL 60000</div>
  <svg class="contact-icon" style="top:181px" width="16" height="16" viewBox="0 0 16 16" aria-label="Phone"><path d="M3 1l3 3-2 2c1 2 3 4 5 5l2-2 3 3-2 3C6 15 1 10 0 3z" fill="#00BBA5"/></svg>
  <div class="contact-row" style="top:181px">(555) 014-2290</div>
  <svg class="contact-icon" style="top:221px" width="18" height="13" viewBox="0 0 18 13" aria-label="Email"><rect width="18" height="13" fill="#00BBA5"/><path d="M0 0 L9 7 L18 0" fill="none" stroke="#1c0b0e" stroke-width="1.5"/></svg>
  <div class="contact-row" style="top:218px">hello@tideandthistle.com</div>

  <div class="footer-rule"></div>
  <div class="copyright">© 2021 Tide &amp; Thistle | All Rights Reserved</div>
</footer>

</body>
</html>
```